CBD AgriBusiness Verdant Trophy Business Card

We are HiTec producer of medical cannabis CBD Switzerland of high quality. Our website is alpinleaf.net, we will also revisit it graphically, the winner of this contest will be the graphic designer chosen for the new design of the website. We stand out by the skill of the team, many of our engineers we win cup cannabis. I join the current map to take as an example but to revisit completely: deletion of surname and first name, modification of funds (front / back), reorganization of text info, highlighting the address of the website. three characteristics define the business card: Professional, Class, refined. The business card must be optimized for soft-touch and selective varnish printing.

Target Market(s)

Customers and Suppliers

Industry/Entity Type

Agribusiness

Contact Information for Business Card

Logo, Tél / Whatsapp, mail, url du site : alpinleaf.net

Font styles to use
Sans Serif

Requirements
Must have
• Logo of alpinleaf.net
Nice to have
• a design that stands out well on the selective varnish
Should not have
• Last name and first name

```html
<!DOCTYPE html>
<html lang="en">
<head>
<meta charset="utf-8">
<title>alpinleaf business card</title>
<link href="https://fonts.googleapis.com/css2?family=Oswald:wght@500&family=Work+Sans:wght@400;500&display=swap" rel="stylesheet">
<style>
  :root {
    --backdrop: #161616;
    --card: #232323;
    --card-edge: #2b2b2b;
    --ink: #f2f2f2;
    --silver: #b9b9b9;
    --leaf: #8cc95a;
  }
  * { margin: 0; padding: 0; box-sizing: border-box; }
  html, body { width: 1200px; height: 900px; overflow: hidden; }
  body {
    background: var(--backdrop);
    font-family: "Work Sans", sans-serif;
    color: var(--ink);
    display: flex;
    flex-direction: column;
    align-items: center;
    justify-content: center;
    gap: 40px;
  }
  .card {
    width: 665px;
    height: 380px;
    background: radial-gradient(circle at 75% 70%, var(--card-edge), var(--card) 70%);
    position: relative;
  }
  .card-front { display: flex; align-items: center; justify-content: center; }
  .brand-name {
    font-family: "Work Sans", sans-serif;
    font-weight: 500;
    font-size: 66px;
    letter-spacing: 1px;
    color: var(--silver);
  }
  .card-back .identity {
    position: absolute;
    right: 370px;
    top: 140px;
    text-align: right;
  }
  .person-name {
    font-family: "Oswald", sans-serif;
    font-weight: 500;
    font-size: 36px;
    letter-spacing: 2px;
    text-transform: uppercase;
    color: var(--leaf);
    line-height: 1.1;
  }
  .person-role { font-size: 17px; margin-top: 4px; }
  .divider {
    position: absolute;
    left: 322px;
    top: 140px;
    width: 2px;
    height: 92px;
    background: var(--leaf);
  }
  .contact-list {
    position: absolute;
    left: 345px;
    top: 138px;
    list-style: none;
    font-size: 17px;
    line-height: 24px;
  }
  .contact-list li { display: flex; align-items: center; gap: 10px; }
  .contact-list svg { width: 12px; height: 12px; flex: none; }
  .site-highlight { color: var(--leaf); }
  .address {
    position: absolute;
    left: 0;
    right: 0;
    bottom: 55px;
    text-align: center;
    font-size: 18px;
    letter-spacing: 1px;
  }
</style>
</head>
<body>
  <section class="card card-front">
    <span class="brand-name">alpinleaf</span>
  </section>

  <section class="card card-back">
    <div class="identity">
      <p class="person-name">Daniel Brooke</p>
      <p class="person-role">Director</p>
    </div>
    <div class="divider"></div>
    <ul class="contact-list">
      <li>
        <svg viewBox="0 0 12 12"><path d="M3 1 L5 3.5 L4 5 Q5 7 7 8 L8.5 7 L11 9 L10 11 Q4 11 1 3 Z" fill="var(--leaf)"/></svg>
        +41 (0) 79 555 01 23
      </li>
      <li>
        <svg viewBox="0 0 12 12"><rect x="3" y="1" width="6" height="10" rx="1" fill="none" stroke="var(--leaf)" stroke-width="1.3"/></svg>
        +44 7700 90 01 42
      </li>
      <li>
        <svg viewBox="0 0 12 12"><rect x="1" y="2.5" width="10" height="7" fill="none" stroke="var(--leaf)" stroke-width="1.2"/><path d="M1 2.5 L6 6.5 L11 2.5" fill="none" stroke="var(--leaf)" stroke-width="1.2"/></svg>
        office@alpinleaf.net
      </li>
      <li>
        <svg viewBox="0 0 12 12"><circle cx="6" cy="6" r="5" fill="none" stroke="var(--leaf)" stroke-width="1.1"/><ellipse cx="6" cy="6" rx="2.2" ry="5" fill="none" stroke="var(--leaf)" stroke-width="1"/><path d="M1 6 H11" stroke="var(--leaf)" stroke-width="1"/></svg>
        <span>www.<span class="site-highlight">alpinleaf</span>.net</span>
      </li>
    </ul>
    <p class="address">27 Fernhill Road, Lakeview, NZ, 4410</p>
  </section>
</body>
</html>
```